Software allocation system needs a business card design

We need a business card designed for our software platform - www.tallivo.com.au

At the moment the logo and website is all black and white, we are happy for suggestions on implementing some colour throughout either the logo or business card.

Industry/Entity Type

Software

Font styles to use
Sans Serif

Colors

Designer to choose colors to be used in the design.

```html
<!DOCTYPE html>
<html lang="en">
<head>
<meta charset="utf-8">
<title>Tallivo Business Card</title>
<link rel="stylesheet" href="https://fonts.googleapis.com/css2?family=Oswald:wght@600&family=Raleway:wght@300;400&display=swap">
<style>
  :root {
    --stage: #e6e2da;
    --card-dark: #2a2a2b;
    --panel-light: #f3f3f3;
    --band-grey: #6e6e70;
    --band-line: #5a5a5c;
    --ink-dark: #2a2a2b;
    --ink-light: #ffffff;
    --icon-bg: #e9e9e9;
  }
  * { margin: 0; padding: 0; box-sizing: border-box; }
  html, body {
    width: 1200px; height: 672px; overflow: hidden;
    background: var(--stage);
  }
  .canvas {
    position: relative; width: 1200px; height: 672px;
    display: flex; align-items: center; justify-content: center;
  }
  .card {
    position: relative; width: 1000px; height: 560px;
    background: var(--card-dark); overflow: hidden;
    box-shadow: 0 14px 30px rgba(0,0,0,0.25);
    font-family: "Raleway", sans-serif;
  }
  .card__shapes { position: absolute; inset: 0; }
  .brand {
    position: absolute; left: 0; top: 110px; width: 560px;
    text-align: center;
    font-family: "Raleway", sans-serif; font-weight: 300;
    font-size: 64px; letter-spacing: 10px; color: var(--ink-dark);
  }
  .phones {
    position: absolute; left: 640px; top: 188px;
    display: flex; flex-direction: column; gap: 16px;
  }
  .contact {
    display: flex; align-items: center; gap: 14px;
    font-size: 19px; letter-spacing: 1.5px; color: var(--ink-light);
  }
  .contact__icon {
    width: 28px; height: 28px; border-radius: 6px;
    background: var(--icon-bg);
    display: flex; align-items: center; justify-content: center;
    flex: none;
  }
  .contact__icon svg { width: 16px; height: 16px; fill: var(--ink-dark); }
  .person {
    position: absolute; left: 56px; top: 352px; color: var(--ink-light);
  }
  .person__name {
    font-family: "Oswald", sans-serif; font-weight: 600;
    font-size: 50px; letter-spacing: 1px; line-height: 1;
    text-transform: uppercase;
  }
  .person__role {
    font-family: "Raleway", sans-serif; font-weight: 400;
    font-size: 26px; letter-spacing: 3px; margin-top: 6px;
    text-transform: uppercase;
  }
  .band {
    position: absolute; left: 0; right: 0; top: 292px; height: 250px;
  }
  .band__left {
    position: absolute; left: 56px; top: 188px;
    display: flex; flex-direction: column; gap: 14px;
  }
  .band__right { position: absolute; left: 640px; top: 14px; }
</style>
</head>
<body>
<main class="canvas">
  <section class="card">
    <svg class="card__shapes" viewBox="0 0 1000 560" aria-hidden="true">
      <!-- light header panel ending in a downward point -->
      <polygon points="0,0 600,0 600,250 520,330 0,330" fill="var(--panel-light)"/>
      <!-- grey contact band along the lower edge -->
      <polygon points="600,290 1000,290 1000,360 600,360" fill="var(--band-grey)"/>
      <line x1="600" y1="366" x2="1000" y2="366" stroke="var(--band-line)" stroke-width="2"/>
      <rect x="0" y="462" width="1000" height="84" fill="var(--band-grey)"/>
      <line x1="0" y1="505" x2="1000" y2="505" stroke="var(--band-line)" stroke-width="2"/>
    </svg>

    <div class="brand">TALLIVO</div>

    <div class="phones">
      <div class="contact">
        <span class="contact__icon"><svg viewBox="0 0 16 16"><path d="M3 1h3l1 4-2 1c1 2 3 4 5 5l1-2 4 1v3c0 1-1 2-2 2C7 15 1 9 1 3c0-1 1-2 2-2z"/></svg></span>
        <span>021 555 0147</span>
      </div>
      <div class="contact">
        <span class="contact__icon"><svg viewBox="0 0 16 16"><path d="M4 1h8v14H4zM6 3v9h4V3zM7 13h2v1H7z"/></svg></span>
        <span>021 555 0147</span>
      </div>
    </div>

    <div class="band">
      <div class="band__right">
        <div class="contact">
          <span class="contact__icon"><svg viewBox="0 0 16 16"><path d="M1 3h14v10H1zM2 4l6 5 6-5v-0.5H2z"/></svg></span>
          <span>hello@tallivo.com.au</span>
        </div>
      </div>
      <div class="band__left">
        <div class="contact">
          <span class="contact__icon"><svg viewBox="0 0 16 16"><path d="M8 1a7 7 0 1 0 0 14A7 7 0 0 0 8 1zm0 1.5c.8 1 1.3 2.4 1.4 4H6.6c.1-1.6.6-3 1.4-4zM2.6 7.5h2.5c.1 1.5.4 2.8 1 3.9A5.5 5.5 0 0 1 2.6 7.5zm0-1a5.5 5.5 0 0 1 3.5-3.9c-.6 1.1-.9 2.4-1 3.9zm8.3 0c-.1-1.5-.4-2.8-1-3.9a5.5 5.5 0 0 1 3.5 3.9zm0 1h2.5a5.5 5.5 0 0 1-3.5 3.9c.6-1.1.9-2.4 1-3.9zM6.6 7.5h2.8c-.1 1.6-.6 3-1.4 4-.8-1-1.3-2.4-1.4-4z"/></svg></span>
          <span>www.tallivo.com.au</span>
        </div>
        <div class="contact">
          <span class="contact__icon"><svg viewBox="0 0 16 16"><path d="M8 1a5 5 0 0 0-5 5c0 4 5 9 5 9s5-5 5-9a5 5 0 0 0-5-5zm0 7a2 2 0 1 1 0-4 2 2 0 0 1 0 4z"/></svg></span>
          <span>27 Harbour Lane, Level 4, Sydney</span>
        </div>
      </div>
    </div>

    <div class="person">
      <h1 class="person__name">Daniel Marsh</h1>
      <p class="person__role">Financial Advisor</p>
    </div>
  </section>
</main>
</body>
</html>
```